R7M Horizon Business Card Design

We need a business card created for our New Business "R7M Horizon"<br/><br/>The business card design is up to you however the following information must be on the business card:<br/><br/>Front of the business card -<br/>Email :darrenp@r7mhorizon.nz<br/>Mobile: +64 (0) 22 4870 619<br/>Website: www.r7mhorizon.nz<br/>Card Owner Name: Darren Paltrow<br/>Company Title: Business Development Manager<br/>Slogan: "Made BETTER on every side". <br/>Logo On the front attached to the design brief<br/><br/>On the back: <br/>Space on the back for 4 more versions of the logo across the bottom of the card indicating different subsidiary brands - R7M Coffee, R7M Arts, R7M ?? (The card will be used for all of these brands - We Will add the extra subsidiary logos to the design once the design is finished (We are a graphics design team). <br/><br/>Other than that we want a premium feeling logo that remains universally usable depending on the business entity that we are using the card for. The use of bright bold colours would be great but we still want the card to feel premium.
Target Market(s)
Gift Design and Manufacturing Companies
Contact Information for Business Card
Front of the business card -
Email :darrenp@r7mhorizon.nz
Mobile: +64 (0) 22 4870 619
Website: www.r7mhorizon.nz
Card Owner Name: Darren Paltrow
Company Title: Business Development Manager
Slogan: "Made BETTER on every side".
Logo On the front attached to the design brief

```html
<!DOCTYPE html>
<html lang="en">
<head>
<meta charset="utf-8">
<title>R7M Horizon — Business Card</title>
<link href="https://fonts.googleapis.com/css2?family=Michroma&family=Open+Sans:wght@400;600&family=Exo+2:wght@400;700&display=swap" rel="stylesheet">
<style>
  :root {
    --brand-blue: #3341a0;
    --brand-blue-light: #4654b3;
    --ink: #2b2b33;
    --paper: #ffffff;
    --backdrop: #2a2a2c;
  }
  * { box-sizing: border-box; margin: 0; padding: 0; }
  html, body {
    width: 1200px; height: 900px; overflow: hidden;
    background: var(--backdrop);
    font-family: "Open Sans", sans-serif;
  }
  .stage { position: relative; width: 1200px; height: 900px; }

  .card {
    position: absolute; left: 250px; width: 700px; height: 400px;
    border-radius: 22px; overflow: hidden;
  }

  /* Back side */
  .card--back {
    top: 35px;
    background: linear-gradient(100deg, var(--brand-blue) 0%, var(--brand-blue) 45%, var(--brand-blue-light) 100%);
    color: var(--paper);
  }
  .card--back .brand {
    position: absolute; left: 0; right: 0; top: 145px;
    display: flex; justify-content: center; align-items: center; gap: 18px;
  }
  .brand-dot {
    width: 44px; height: 44px; border-radius: 50%;
    border: 6px solid currentColor; flex: none;
  }
  .brand-name {
    font-family: "Open Sans", sans-serif; font-weight: 600;
    font-size: 54px; letter-spacing: 1px; line-height: 1; white-space: nowrap;
  }
  .card--back .slogan {
    position: absolute; left: 0; right: 0; top: 318px;
    display: flex; justify-content: center; align-items: center; gap: 12px;
    font-family: "Exo 2", sans-serif; font-size: 21px; letter-spacing: 0.5px;
  }
  .slogan b, .slogan-pill b { font-weight: 700; }
  .arrow { width: 0; height: 0; border-top: 6px solid transparent; border-bottom: 6px solid transparent; }
  .arrow--left { border-right: 12px solid var(--paper); }
  .arrow--right { border-left: 12px solid var(--paper); }

  /* Front side */
  .card--front { top: 465px; background: var(--paper); color: var(--ink); }
  .card--front .brand {
    position: absolute; left: 40px; top: 118px;
    display: flex; align-items: center; gap: 12px; color: var(--brand-blue);
  }
  .card--front .brand-dot { width: 34px; height: 34px; border-width: 5px; }
  .card--front .brand-name { font-size: 36px; }

  .person { position: absolute; left: 372px; top: 95px; width: 300px; }
  .person-name {
    font-family: "Michroma", sans-serif; font-size: 20px; font-weight: 400;
    color: var(--brand-blue); letter-spacing: 1px; text-transform: uppercase;
    -webkit-text-stroke: 0.8px var(--brand-blue); white-space: nowrap;
  }
  .person-title { font-size: 17px; margin-top: 4px; color: var(--ink); white-space: nowrap; }
  .divider { height: 2px; background: var(--brand-blue); margin-top: 14px; width: 290px; }

  .contacts { list-style: none; margin-top: 18px; width: 290px; }
  .contacts li {
    display: flex; justify-content: flex-end; align-items: center; gap: 10px;
    font-size: 18px; line-height: 30px; color: var(--ink); white-space: nowrap;
  }
  .contacts svg { width: 16px; height: 16px; flex: none; }

  .footer-rule {
    position: absolute; left: 0; right: 0; top: 307px; height: 4px; background: var(--brand-blue);
  }
  .slogan-pill {
    position: absolute; left: 190px; top: 285px; width: 310px; height: 48px;
    border-radius: 24px; background: var(--brand-blue); color: var(--paper);
    display: flex; justify-content: center; align-items: center;
    font-family: "Exo 2", sans-serif; font-size: 21px; white-space: nowrap;
  }
</style>
</head>
<body>
<main class="stage">

  <section class="card card--back" aria-label="Card back">
    <div class="brand">
      <span class="brand-dot"></span>
      <span class="brand-name">R7M Horizon</span>
    </div>
    <p class="slogan"><span class="arrow arrow--left"></span><span>Made <b>BETTER</b> on every side</span><span class="arrow arrow--right"></span></p>
  </section>

  <section class="card card--front" aria-label="Card front">
    <div class="brand">
      <span class="brand-dot"></span>
      <span class="brand-name">R7M Horizon</span>
    </div>

    <div class="person">
      <h1 class="person-name">Darren Paltrow</h1>
      <p class="person-title">Business Development Manager</p>
      <div class="divider"></div>
      <ul class="contacts">
        <li>+64 (0) 22 4870 619
          <svg viewBox="0 0 24 24" fill="var(--brand-blue)"><path d="M6.6 10.8a15.5 15.5 0 0 0 6.6 6.6l2.2-2.2c.3-.3.7-.4 1-.2 1.1.4 2.3.6 3.6.6.6 0 1 .4 1 1V20c0 .6-.4 1-1 1A17 17 0 0 1 3 4c0-.6.4-1 1-1h3.5c.6 0 1 .4 1 1 0 1.3.2 2.5.6 3.6.1.3 0 .7-.2 1z"/></svg>
        </li>
        <li>darrenp@r7mhorizon.nz
          <svg viewBox="0 0 24 24" fill="none" stroke="var(--brand-blue)" stroke-width="2.2"><rect x="3" y="5" width="18" height="14" rx="1"/><path d="M3 6l9 7 9-7"/></svg>
        </li>
        <li>www.r7mhorizon.nz
          <svg viewBox="0 0 24 24" fill="none" stroke="var(--brand-blue)" stroke-width="2"><circle cx="12" cy="12" r="9"/><ellipse cx="12" cy="12" rx="4" ry="9"/><path d="M3 12h18M4.5 7.5h15M4.5 16.5h15"/></svg>
        </li>
      </ul>
    </div>

    <div class="footer-rule"></div>
    <p class="slogan-pill"><span>Made <b>BETTER</b> on every side</span></p>
  </section>

</main>
</body>
</html>
```